Global (re)insurance broker needs a business card design

We need a classic business card for our company that is headquartered in SG, with offices in Malaysia and Dubai. We specialise in insurance and reinsurance broking and consultancy for our global clients.

```html
<!DOCTYPE html>
<html lang="en">
<head>
<meta charset="utf-8">
<title>Norvane business card</title>
<link rel="stylesheet" href="https://fonts.googleapis.com/css2?family=Open+Sans:wght@400;600;700;800&display=swap">
<style>
  :root {
    --page: #2a2a2e;
    --card: #151515;
    --blue: #2a4a9c;
    --mint: #c5dcb8;
    --ink: #ededed;
  }
  html, body {
    margin: 0;
    padding: 0;
    width: 1200px;
    height: 947px;
    overflow: hidden;
    background: var(--page);
    font-family: "Open Sans", Arial, sans-serif;
  }
  .sheet {
    width: 1200px;
    height: 947px;
    display: flex;
    flex-direction: column;
    align-items: center;
    justify-content: center;
    gap: 50px;
  }
  .card {
    position: relative;
    width: 720px;
    height: 412px;
    background: var(--card);
    border-radius: 26px;
    overflow: hidden;
    box-shadow: 0 14px 34px rgba(0,0,0,.45);
  }
  .card-front {
    display: flex;
    align-items: center;
    justify-content: center;
  }
  .wordmark {
    font-weight: 800;
    color: var(--mint);
    letter-spacing: 2px;
    line-height: 1;
    white-space: nowrap;
  }
  .card-front .wordmark { font-size: 112px; }
  .card-back .swoosh {
    position: absolute;
    inset: 0;
    width: 100%;
    height: 100%;
  }
  .card-back .wordmark {
    position: absolute;
    left: 70px;
    top: 186px;
    font-size: 42px;
    letter-spacing: 1px;
  }
  .divider {
    position: absolute;
    left: 368px;
    top: 70px;
    width: 2px;
    height: 272px;
    background: var(--mint);
  }
  .details {
    position: absolute;
    left: 394px;
    top: 78px;
    color: var(--ink);
  }
  .person-name {
    margin: 0;
    font-size: 25px;
    font-weight: 800;
    line-height: 1.1;
  }
  .person-name .first { color: var(--blue); }
  .person-name .last { color: var(--mint); }
  .person-role {
    margin: 2px 0 18px;
    font-size: 16px;
    font-weight: 400;
  }
  .contact-list {
    list-style: none;
    margin: 0 0 20px;
    padding: 0;
    font-size: 15px;
    line-height: 1.5;
  }
  .contact-list li {
    display: flex;
    align-items: center;
    gap: 8px;
  }
  .contact-list svg { width: 12px; height: 12px; flex: none; }
  .address {
    margin: 0;
    font-style: normal;
    font-size: 15px;
    line-height: 1.45;
  }
</style>
</head>
<body>
<main class="sheet">
  <section class="card card-front" aria-label="Card front">
    <span class="wordmark">NORVANE</span>
  </section>

  <section class="card card-back" aria-label="Card back">
    <svg class="swoosh" viewBox="0 0 720 412" aria-hidden="true">
      <path d="M0 150 Q40 300 112 412 L0 412 Z" fill="var(--blue)"/>
      <path d="M0 132 Q62 300 142 412" fill="none" stroke="var(--mint)" stroke-width="5"/>
      <path d="M720 262 Q680 112 608 0 L720 0 Z" fill="var(--blue)"/>
      <path d="M720 280 Q658 112 578 0" fill="none" stroke="var(--mint)" stroke-width="5"/>
    </svg>

    <span class="wordmark">NORVANE</span>
    <div class="divider"></div>

    <div class="details">
      <h1 class="person-name"><span class="first">Mira</span> <span class="last">Lowell</span></h1>
      <p class="person-role">Chief Operating Officer</p>
      <ul class="contact-list">
        <li>
          <svg viewBox="0 0 24 24"><path fill="var(--mint)" d="M6.6 10.8a15.1 15.1 0 0 0 6.6 6.6l2.2-2.2c.3-.3.7-.4 1-.2 1.1.4 2.3.6 3.6.6.6 0 1 .4 1 1V20c0 .6-.4 1-1 1A17 17 0 0 1 3 4c0-.6.4-1 1-1h3.5c.6 0 1 .4 1 1 0 1.3.2 2.5.6 3.6.1.3 0 .7-.2 1z"/></svg>
          +65 5550 2184
        </li>
        <li>
          <svg viewBox="0 0 24 24"><path fill="var(--mint)" d="M2 5h20v14H2z"/><path fill="none" stroke="var(--card)" stroke-width="2" d="M2 5l10 8 10-8"/></svg>
          mira@norvane.com
        </li>
        <li>
          <svg viewBox="0 0 24 24"><circle cx="12" cy="12" r="10" fill="var(--mint)"/><path fill="none" stroke="var(--card)" stroke-width="1.6" d="M2 12h20M12 2c3 3 3 17 0 20M12 2c-3 3-3 17 0 20"/></svg>
          www.norvane.com
        </li>
      </ul>
      <address class="address">
        24 Harbour Lane,<br>
        Meridian Tower #08-02,<br>
        Singapore 018956
      </address>
    </div>
  </section>
</main>
</body>
</html>
```